Talon Microsystems PowerPoint Master Slide Deck Design

This is a 2-phase project to design a slide deck for a semiconductor company in the Silicon Valley. The design budget will be increased with each phase.
The slide deck will need to have one version with a dark background for presentations and a second version with a white background. Otherwise, the slides will be the same. I anticipate we will need a total of 10 slides, but that number may change.
The first phase will be to design a Title and a Title and Content slide.
- The Title Slide is the first slide of the deck. It should include the presentation title, the presenter's name and date of presentation
- The Title and Content slide should include a title and content with bullet points and up to 2 additional sub-bullets
- The Title and Content slide should have a footer that includes the slide #, Talon Microsystems Confidential, and the logo. This footer will be on every slide except the Title Slide
The first two slides will serve as the format for the remaining ~8 slides:
-Header and Content Text (1, 2, 4 column)
-Header and Content Image (bar chart, pie chart, tables)
-Break
-Title only
-Closing (Talon logo only)
Our slides contain a lot of content so a clean and simple design is best.
Both phases will need to include pre-set color options for
-Text and Lines
-Shadows
-Bullets and sub-bullets (including shapes, ex. circle, slash, square, etc.)
-Bar charts, pie charts, tables
Samples of our collateral are attached. Logo files are also attached
Look and feel
Each slider illustrates characteristics of the customer's brand and the style your logo design should communicate.

```html
<!DOCTYPE html>
<html lang="en">
<head>
<meta charset="utf-8">
<title>Talon Microsystems — Master Slide Deck</title>
<link rel="stylesheet" href="https://fonts.googleapis.com/css2?family=Montserrat:wght@400;500;600;700;800&display=swap">
<style>
  :root{
    --canvas:#000000;
    --slide:#0a2fe4;
    --slide-deep:#0624c8;
    --slide-light:#1c55f0;
    --accent:#6fd0f2;
    --accent-bright:#35d6ff;
    --white:#ffffff;
    --rule:rgba(255,255,255,.55);
    --rule-soft:rgba(255,255,255,.3);
    --box-line:rgba(120,170,255,.55);
    --arc:#1a6cf5;
  }
  *{margin:0;padding:0;box-sizing:border-box}
  html,body{width:875px;height:1200px;overflow:hidden;background:var(--canvas)}
  body{font-family:"Montserrat",Arial,sans-serif;color:var(--white);position:relative}

  .slide{position:absolute;width:385px;height:217px;overflow:hidden;
    background:linear-gradient(135deg,var(--slide-deep) 0%,var(--slide) 45%,var(--slide-light) 100%)}
  .slide.has-bar::before{content:"";position:absolute;left:0;top:0;width:100%;height:2.5px;
    background:linear-gradient(90deg,var(--slide-deep),var(--accent-bright))}
  .col-a{left:33px}.col-b{left:436px}
  .row-1{top:21px}.row-2{top:257px}.row-3{top:493px}.row-4{top:729px}.row-5{top:964px}

  .abs{position:absolute}
  .hl{color:var(--accent)}

  /* title block */
  .title-rule{position:absolute;top:24px;width:36px;height:1px;background:var(--white)}
  .slide-title{position:absolute;top:30px;font-size:19px;font-weight:800;letter-spacing:1px;white-space:nowrap;line-height:1}

  /* footer */
  .footer-rule{position:absolute;left:30px;right:30px;top:192px;height:.6px;background:var(--rule-soft)}
  .footer-brand{position:absolute;left:54px;top:200px;font-size:6px;font-weight:700;letter-spacing:.3px}
  .footer-note{position:absolute;left:127px;top:201px;font-size:5px;letter-spacing:.9px;font-weight:500}
  .footer-page{position:absolute;left:315px;top:201px;font-size:5px;letter-spacing:.8px;font-weight:700}

  /* bullets */
  .bullet{position:absolute;padding-left:14px;line-height:1.2}
  .bullet::before{content:"";position:absolute;left:0;top:.6em;width:7px;height:.8px;background:var(--white)}
  .bullet::after{content:"";position:absolute;left:7px;top:calc(.6em - 2px);width:4px;height:4px;border:.8px solid var(--white);border-radius:50%}
  .bullet.small{padding-left:8px}
  .bullet.small::before{width:4px;top:.55em}
  .bullet.small::after{left:4px;width:3px;height:3px;top:calc(.55em - 1.5px)}

  .num{position:absolute;font-weight:700;color:var(--accent);line-height:1}

  /* slide 1 */
  .cover-rule{position:absolute;left:69px;top:46px;width:1.5px;height:124px;background:var(--white)}
  .cover-brand{position:absolute;left:89px;top:48px;font-weight:700;line-height:1}
  .cover-brand .name{font-size:17px;letter-spacing:.5px;display:block}
  .cover-brand .sub{font-size:7px;display:block;margin-top:2px;padding-left:2px}
  .cover-title{position:absolute;left:86px;top:94px;font-size:24px;font-weight:800;line-height:1.2;letter-spacing:.5px}
  .cover-meta{position:absolute;top:163px;font-size:7px;font-weight:600;letter-spacing:1.3px}
  .cover-divider{position:absolute;left:204px;top:159px;width:1px;height:16px;background:var(--white)}

  /* slide 2 */
  .card{position:absolute;width:166px;height:48px;border:.7px solid var(--box-line)}
  .card .num{left:8px;top:14px;font-size:24px}
  .card .card-head{position:absolute;left:48px;top:7px;font-size:7px;font-weight:600;color:var(--accent)}
  .card .card-text{position:absolute;left:48px;top:17px;width:112px;font-size:3.4px;line-height:1.3}
  .card .bullet{font-size:3.4px;left:53px}

  /* slide 3 */
  .wide-para{position:absolute;left:88px;width:245px;font-size:7px;line-height:1.25}
  .wide-bullet{left:113px;font-size:6.8px}

  /* slide 4 */
  .col-para{position:absolute;width:115px;font-size:7px;line-height:1.25}
  .col-bullet{font-size:6.2px;width:115px}

  /* slide 5 */
  .quad-num{position:absolute;top:69px;font-size:20px}
  .quad-icon{position:absolute;top:71px;width:16px;height:16px}
  .quad-sub{position:absolute;top:95px;font-size:6.5px;font-weight:600;color:var(--accent)}
  .quad-para{position:absolute;top:115px;width:78px;font-size:4.9px;line-height:1.2}
  .quad-bullet{font-size:3.7px;width:72px}
  .quad-div{position:absolute;top:79px;width:.6px;height:88px;background:var(--rule-soft)}

  /* slide 6 */
  .photo-area{position:absolute;left:197px;top:3px;width:188px;height:189px;
    background:radial-gradient(circle at 55% 45%,#4ff0e0 0%,#1b8fa6 28%,#0d4f73 60%,#0a2f52 100%)}
  .stack-title{position:absolute;left:40px;top:70px;font-size:20px;font-weight:800;line-height:1.22;letter-spacing:1px}

  /* slide 7 */
  .chart-cap{position:absolute;left:0;width:385px;top:68px;text-align:center;font-size:7px;font-weight:500}
  .chart{position:absolute;left:0;top:0}
  .chart text{font-family:"Montserrat",Arial,sans-serif;font-weight:700;fill:var(--white)}

  /* slide 8 */
  .break-title{position:absolute;left:0;width:385px;top:117px;text-align:center;font-size:20px;font-weight:800;letter-spacing:1px}
  .break-title i{color:var(--accent)}

  /* slide 9 */
  .arcs{position:absolute;left:0;top:0}
  .center-title{position:absolute;left:0;width:368px;top:96px;text-align:center;font-size:23px;font-weight:800;letter-spacing:.5px}

  /* slide 10 */
  .closing-brand{position:absolute;left:0;width:385px;top:62px;text-align:center;font-weight:700;line-height:1}
  .closing-brand .name{display:block;font-size:44px;letter-spacing:2px}
  .closing-brand .sub{display:block;font-size:19px;margin-top:4px;letter-spacing:.5px}
</style>
</head>
<body>

<!-- Title slide -->
<section class="slide col-a row-1">
  <div class="cover-rule"></div>
  <div class="cover-brand"><span class="name">TALON</span><span class="sub">Microsystems</span></div>
  <h1 class="cover-title">BUSINESS<br><span class="hl">PRESENTATION</span></h1>
  <div class="cover-meta" style="left:117px">PRESENTER’S NAME</div>
  <div class="cover-divider"></div>
  <div class="cover-meta" style="left:220px;letter-spacing:.9px">DATE: 12-20-2024</div>
</section>

<!-- Four-box content slide -->
<section class="slide has-bar col-b row-1">
  <div class="title-rule" style="left:66px"></div>
  <h2 class="slide-title" style="left:67px">YOUR <span class="hl">CONTENT</span> SLIDE</h2>

  <div class="card" style="left:23px;top:68px">
    <span class="num">01</span><span class="card-head">CONTENT HEADER</span>
    <p class="card-text">Lorem ipsum dolor sit amet, consectetuer adipiscing elit. Aenean commodo ligula eget dolor. Aenean massa.</p>
    <span class="bullet small" style="top:29px">Lorem ipsum dolor sit amet, consectetuer adipiscing elit.</span>
    <span class="bullet small" style="top:37px">Lorem ipsum dolor sit amet, consectetuer adipiscing elit.</span>
  </div>
  <div class="card" style="left:196px;top:68px">
    <span class="num">02</span><span class="card-head">CONTENT HEADER</span>
    <p class="card-text">Lorem ipsum dolor sit amet, consectetuer adipiscing elit. Aenean commodo ligula eget dolor. Aenean massa.</p>
    <span class="bullet small" style="top:29px">Lorem ipsum dolor sit amet, consectetuer adipiscing elit.</span>
    <span class="bullet small" style="top:37px">Lorem ipsum dolor sit amet, consectetuer adipiscing elit.</span>
  </div>
  <div class="card" style="left:23px;top:122px">
    <span class="num">03</span><span class="card-head">CONTENT HEADER</span>
    <p class="card-text">Lorem ipsum dolor sit amet, consectetuer adipiscing elit. Aenean commodo ligula eget dolor. Aenean massa.</p>
    <span class="bullet small" style="top:29px">Lorem ipsum dolor sit amet, consectetuer adipiscing elit.</span>
    <span class="bullet small" style="top:37px">Lorem ipsum dolor sit amet, consectetuer adipiscing elit.</span>
  </div>
  <div class="card" style="left:196px;top:122px">
    <span class="num">04</span><span class="card-head">CONTENT HEADER</span>
    <p class="card-text">Lorem ipsum dolor sit amet, consectetuer adipiscing elit. Aenean commodo ligula eget dolor. Aenean massa.</p>
    <span class="bullet small" style="top:29px">Lorem ipsum dolor sit amet, consectetuer adipiscing elit.</span>
    <span class="bullet small" style="top:37px">Lorem ipsum dolor sit amet, consectetuer adipiscing elit.</span>
  </div>

  <div class="footer-rule"></div>
  <div class="footer-brand">TALON</div>
  <div class="footer-note">©Copyright 2023 Talon Microsystems.</div>
  <div class="footer-page">SLIDE #</div>
</section>

<!-- One-column content slide -->
<section class="slide has-bar col-a row-2">
  <div class="title-rule" style="left:51px"></div>
  <h2 class="slide-title" style="left:51px">CONTENT <span class="hl">HEADER</span> SLIDE</h2>

  <span class="num" style="left:39px;top:82px;font-size:22px">01</span>
  <p class="wide-para" style="top:64px">Lorem ipsum dolor sit amet, consectetuer adipiscing elit. Aenean commodo ligula eget dolor. Aenean massa.</p>
  <span class="bullet wide-bullet" style="top:94px">Lorem ipsum dolor sit amet, consectetuer adipiscing elit.</span>
  <span class="bullet wide-bullet" style="top:107px">Lorem ipsum dolor sit amet, consectetuer adipiscing elit.</span>

  <div class="abs" style="left:34px;top:124px;width:322px;height:.6px;background:var(--rule-soft)"></div>

  <span class="num" style="left:39px;top:147px;font-size:22px">02</span>
  <p class="wide-para" style="top:131px">Lorem ipsum dolor sit amet, consectetuer adipiscing elit. Aenean commodo ligula eget dolor. Aenean massa.</p>
  <span class="bullet wide-bullet" style="top:159px">Lorem ipsum dolor sit amet, consectetuer adipiscing elit.</span>
  <span class="bullet wide-bullet" style="top:172px">Lorem ipsum dolor sit amet, consectetuer adipiscing elit.</span>

  <div class="footer-rule"></div>
  <div class="footer-brand">TALON</div>
  <div class="footer-note">©Copyright 2023 Talon Microsystems.</div>
  <div class="footer-page">SLIDE #</div>
</section>

<!-- Two-column content slide -->
<section class="slide has-bar col-b row-2">
  <div class="title-rule" style="left:51px"></div>
  <h2 class="slide-title" style="left:51px">CONTENT <span class="hl">HEADER</span> SLIDE</h2>

  <span class="num" style="left:32px;top:78px;font-size:22px">01</span>
  <p class="col-para" style="left:67px;top:76px">Lorem ipsum dolor sit amet, consectetuer adipiscing elit. Aenean commodo ligula eget dolor. Aenean massa.</p>
  <span class="bullet col-bullet" style="left:67px;top:125px;padding-left:17px">Lorem ipsum dolor sit amet, consectetuer adipiscing elit.</span>
  <span class="bullet col-bullet" style="left:67px;top:150px;padding-left:17px">Lorem ipsum dolor sit amet, consectetuer adipiscing elit.</span>

  <div class="abs" style="left:195px;top:77px;width:.6px;height:103px;background:var(--rule-soft)"></div>

  <span class="num" style="left:207px;top:78px;font-size:22px">02</span>
  <p class="col-para" style="left:242px;top:76px">Lorem ipsum dolor sit amet, consectetuer adipiscing elit. Aenean commodo ligula eget dolor. Aenean massa.</p>
  <span class="bullet col-bullet" style="left:242px;top:125px;padding-left:17px">Lorem ipsum dolor sit amet, consectetuer adipiscing elit.</span>
  <span class="bullet col-bullet" style="left:242px;top:150px;padding-left:17px">Lorem ipsum dolor sit amet, consectetuer adipiscing elit.</span>

  <div class="footer-rule"></div>
  <div class="footer-brand">TALON</div>
  <div class="footer-note">©Copyright 2023 Talon Microsystems.</div>
  <div class="footer-page">SLIDE #</div>
</section>

<!-- Four-column content slide -->
<section class="slide has-bar col-a row-3">
  <div class="title-rule" style="left:51px"></div>
  <h2 class="slide-title" style="left:51px">CONTENT <span class="hl">HEADER</span> SLIDE</h2>

  <span class="num quad-num" style="left:30px">01</span>
  <svg class="quad-icon" style="left:62px;width:30px" viewBox="0 0 30 16" fill="none" stroke="#fff" stroke-width="1">
    <circle cx="7" cy="5" r="3"/><circle cx="15" cy="5" r="3"/><circle cx="23" cy="5" r="3"/>
    <path d="M2 14c0-3 2-5 5-5s5 2 5 5M10 14c0-3 2-5 5-5s5 2 5 5M18 14c0-3 2-5 5-5s5 2 5 5"/>
  </svg>
  <span class="quad-sub" style="left:26px">Subsection Title</span>
  <p class="quad-para" style="left:26px">Lorem ipsum dolor sit amet, consectetuer adipiscing elit. Aenean commodo ligula eget dolor. Aenean massa.</p>
  <span class="bullet small quad-bullet" style="left:29px;top:145px;padding-left:12px">Lorem ipsum dolor sit amet, consectetuer adipiscing elit.</span>
  <span class="bullet small quad-bullet" style="left:29px;top:160px;padding-left:12px">Lorem ipsum dolor sit amet, consectetuer adipiscing elit.</span>
  <div class="quad-div" style="left:106px"></div>

  <span class="num quad-num" style="left:127px">02</span>
  <svg class="quad-icon" style="left:164px" viewBox="0 0 16 16" fill="none" stroke="#fff" stroke-width="1">
    <circle cx="8" cy="8" r="6.5"/><path d="M8 4v4l2.5 2"/>
  </svg>
  <span class="quad-sub" style="left:114px">Subsection Title</span>
  <p class="quad-para" style="left:114px">Lorem ipsum dolor sit amet, consectetuer adipiscing elit. Aenean commodo ligula eget dolor. Aenean massa.</p>
  <span class="bullet small quad-bullet" style="left:117px;top:145px;padding-left:12px">Lorem ipsum dolor sit amet, consectetuer adipiscing elit.</span>
  <span class="bullet small quad-bullet" style="left:117px;top:160px;padding-left:12px">Lorem ipsum dolor sit amet, consectetuer adipiscing elit.</span>
  <div class="quad-div" style="left:195px"></div>

  <span class="num quad-num" style="left:212px">03</span>
  <svg class="quad-icon" style="left:250px" viewBox="0 0 16 16" fill="none" stroke="#fff" stroke-width="1">
    <path d="M14 2c-5 0-8 3-9 7l2 2c4-1 7-4 7-9z"/><circle cx="10.5" cy="5.5" r="1.3"/>
    <path d="M5 9H2l2-3h3M7 11v3l3-2V9M4 12l-2 2"/>
  </svg>
  <span class="quad-sub" style="left:202px">Subsection Title</span>
  <p class="quad-para" style="left:202px">Lorem ipsum dolor sit amet, consectetuer adipiscing elit. Aenean commodo ligula eget dolor. Aenean massa.</p>
  <span class="bullet small quad-bullet" style="left:205px;top:145px;padding-left:12px">Lorem ipsum dolor sit amet, consectetuer adipiscing elit.</span>
  <span class="bullet small quad-bullet" style="left:205px;top:160px;padding-left:12px">Lorem ipsum dolor sit amet, consectetuer adipiscing elit.</span>
  <div class="quad-div" style="left:284px"></div>

  <span class="num quad-num" style="left:294px">04</span>
  <svg class="quad-icon" style="left:333px" viewBox="0 0 16 16" fill="none" stroke="#fff" stroke-width="1">
    <path d="M3 13l1-3a6 6 0 1 1 2 2z"/><path d="M6 6h5M6 8.5h4"/>
  </svg>
  <span class="quad-sub" style="left:290px">Subsection Title</span>
  <p class="quad-para" style="left:290px">Lorem ipsum dolor sit amet, consectetuer adipiscing elit. Aenean commodo ligula eget dolor. Aenean massa.</p>
  <span class="bullet small quad-bullet" style="left:293px;top:145px;padding-left:12px">Lorem ipsum dolor sit amet, consectetuer adipiscing elit.</span>
  <span class="bullet small quad-bullet" style="left:293px;top:160px;padding-left:12px">Lorem ipsum dolor sit amet, consectetuer adipiscing elit.</span>

  <div class="footer-rule"></div>
  <div class="footer-brand">TALON</div>
  <div class="footer-note">©Copyright 2023 Talon Microsystems.</div>
  <div class="footer-page">SLIDE #</div>
</section>

<!-- Header and image slide -->
<section class="slide has-bar col-b row-3">
  <div class="title-rule" style="left:43px;top:62px"></div>
  <h2 class="stack-title">CONTENT<br><span class="hl">HEADER</span><br>SLIDE</h2>
  <div class="photo-area" role="img" aria-label="Photo of a hand touching a glowing circuit-board brain inside a digital ring"></div>

  <div class="footer-rule"></div>
  <div class="footer-brand">TALON</div>
  <div class="footer-note">©Copyright 2023 Talon Microsystems.</div>
  <div class="footer-page">SLIDE #</div>
</section>

<!-- Chart slide -->
<section class="slide has-bar col-a row-4">
  <div class="title-rule" style="left:51px"></div>
  <h2 class="slide-title" style="left:51px">CONTENT <span class="hl">HEADER</span> SLIDE</h2>
  <p class="chart-cap">YOUR CONTENT GRAPHS STYLE</p>

  <svg class="chart" width="385" height="217" viewBox="0 0 385 217">
    <defs>
      <pattern id="chart-grid" x="51" y="86" width="16.8" height="8.3" patternUnits="userSpaceOnUse">
        <path d="M16.8 0V8.3M0 8.3H16.8" fill="none" stroke="rgba(120,180,255,.45)" stroke-width=".5"/>
      </pattern>
      <linearGradient id="area-fill" x1="0" y1="0" x2="0" y2="1">
        <stop offset="0" stop-color="#1e7bff" stop-opacity=".9"/>
        <stop offset="1" stop-color="#1e7bff" stop-opacity=".35"/>
      </linearGradient>
    </defs>
    <rect x="51" y="86" width="168" height="83" fill="url(#chart-grid)" stroke="rgba(120,180,255,.5)" stroke-width=".5"/>
    <path d="M50 136L67 129.8L84 148.5L101 136L118 136L135 111L152 117.3L169 104.8L186 117.3L203 117.3V169H50Z" fill="url(#area-fill)"/>
    <polyline points="50,136 67,129.8 84,148.5 101,136 118,136 135,111 152,117.3 169,104.8 186,117.3 203,117.3" fill="none" stroke="#fff" stroke-width=".9"/>
    <g fill="#fff">
      <circle cx="50" cy="136" r="1.8"/><circle cx="67" cy="129.8" r="1.8"/><circle cx="84" cy="148.5" r="1.8"/>
      <circle cx="101" cy="136" r="1.8"/><circle cx="118" cy="136" r="1.8"/><circle cx="135" cy="111" r="1.8"/>
      <circle cx="152" cy="117.3" r="1.8"/><circle cx="169" cy="104.8" r="1.8"/><circle cx="186" cy="117.3" r="1.8"/>
      <circle cx="203" cy="117.3" r="1.8"/>
    </g>
    <g font-size="5" text-anchor="middle">
      <text x="29" y="88">70</text><text x="29" y="100.5">60</text><text x="29" y="113">50</text>
      <text x="29" y="125.5">40</text><text x="29" y="138">30</text><text x="29" y="150.5">20</text>
      <text x="29" y="163">10</text><text x="31" y="178">0</text>
      <text x="50" y="178">2015</text><text x="67" y="178">2016</text><text x="84" y="178">2017</text>
      <text x="101" y="178">2018</text><text x="118" y="178">2019</text><text x="135" y="178">2020</text>
      <text x="152" y="178">2021</text><text x="169" y="178">2022</text><text x="186" y="178">2023</text>
      <text x="203" y="178">2024</text>
    </g>

    <g fill="#fff">
      <rect x="239" y="86" width="15" height="83"/><rect x="261" y="86" width="15" height="83"/>
      <rect x="284" y="86" width="15" height="83"/><rect x="306" y="86" width="15" height="83"/>
      <rect x="329" y="86" width="15" height="83"/><rect x="352" y="86" width="15" height="83"/>
    </g>
    <g fill="var(--accent)">
      <rect x="239" y="156.5" width="15" height="12.5"/><rect x="261" y="148.2" width="15" height="20.8"/>
      <rect x="284" y="140" width="15" height="29"/><rect x="306" y="123.4" width="15" height="45.6"/>
      <rect x="329" y="115" width="15" height="54"/><rect x="352" y="106.8" width="15" height="62.2"/>
    </g>
    <g font-size="4.3" text-anchor="middle">
      <text x="246.5" y="163.5">15%</text><text x="268.5" y="155">25%</text><text x="291.5" y="147">35%</text>
      <text x="313.5" y="131">55%</text><text x="336.5" y="122">65%</text><text x="359.5" y="114">75%</text>
    </g>
    <g font-size="5" text-anchor="middle">
      <text x="246.5" y="178">2019</text><text x="268.5" y="178">2020</text><text x="291.5" y="178">2021</text>
      <text x="313.5" y="178">2022</text><text x="336.5" y="178">2023</text><text x="359.5" y="178">2024</text>
    </g>
  </svg>

  <div class="footer-rule"></div>
  <div class="footer-brand">TALON</div>
  <div class="footer-note">©Copyright 2023 Talon Microsystems.</div>
  <div class="footer-page">SLIDE #</div>
</section>

<!-- Break slide -->
<section class="slide has-bar col-b row-4">
  <svg class="abs" style="left:168px;top:48px" width="52" height="62" viewBox="0 0 52 62" fill="none" stroke="#fff" stroke-width="1.6" stroke-linecap="round">
    <path d="M14 4c-3 3 3 5 0 8s3 5 0 8"/><path d="M22 4c-3 3 3 5 0 8s3 5 0 8"/><path d="M30 4c-3 3 3 5 0 8s3 5 0 8"/>
    <circle cx="14" cy="3" r="1.3"/><circle cx="22" cy="3" r="1.3"/><circle cx="30" cy="3" r="1.3"/>
    <path d="M8 28h32v16a12 12 0 0 1-12 12h-8A12 12 0 0 1 8 44z"/>
    <path d="M40 32h3a6 6 0 0 1 0 12h-4"/>
    <rect x="19" y="36" width="8" height="10"/><path d="M23 28v8"/>
    <path d="M2 59h44"/>
  </svg>
  <h2 class="break-title">BREAK <i>SLIDE</i></h2>

  <div class="footer-rule"></div>
  <div class="footer-brand">TALON</div>
  <div class="footer-note">©Copyright 2023 Talon Microsystems.</div>
  <div class="footer-page">SLIDE #</div>
</section>

<!-- Title-only slide -->
<section class="slide has-bar col-a row-5">
  <svg class="arcs" width="385" height="217" viewBox="0 0 385 217">
    <path d="M270 0C320 8 360 25 385 50V0Z" fill="var(--arc)" opacity=".8"/>
    <path d="M0 118C40 135 60 160 68 190H52C45 165 25 145 0 135Z" fill="var(--arc)"/>
    <path d="M0 135C25 145 45 165 52 190H0Z" fill="#1747d8" opacity=".7"/>
  </svg>
  <h2 class="center-title">YOUR <span class="hl">TITLE</span> SLIDE</h2>

  <div class="footer-rule"></div>
  <div class="footer-brand">TALON</div>
  <div class="footer-note">©Copyright 2023 Talon Microsystems.</div>
  <div class="footer-page">SLIDE #</div>
</section>

<!-- Closing slide -->
<section class="slide has-bar col-b row-5">
  <svg class="arcs" width="385" height="217" viewBox="0 0 385 217">
    <path d="M230 0C290 10 350 30 385 60V0Z" fill="var(--arc)" opacity=".6"/>
  </svg>
  <div class="closing-brand"><span class="name">TALON</span><span class="sub">Microsystems</span></div>

  <div class="footer-rule"></div>
  <div class="footer-brand">TALON</div>
  <div class="footer-note">©Copyright 2023 Talon Microsystems.</div>
  <div class="footer-page">SLIDE #</div>
</section>

</body>
</html>
```